VOR Exterior Coatings

double sided. the front i want the name of the business each word on a new line with the VOR being bigger. id like teal, black and white colors. the back i want my contact info. Flat, no gloss. Something professional and I want to feel the letters bump put of the card. if possible maybe a paint sprayer in corner. not a car paint spray. (no tank on top of gun)
no vehicle paint sprayers. that means no tank on top of the gun. doesn't have to have a sprayer. black/dark background on the front. white back ground on back with info

```html
<!DOCTYPE html>
<html lang="en">
<head>
<meta charset="utf-8">
<title>VOR Exterior Coatings – Business Cards</title>
<link rel="stylesheet" href="https://fonts.googleapis.com/css2?family=Archivo:wght@400;800&display=swap">
<style>
  :root {
    --stage: #1c1c1d;
    --card-dark: #0a0a0a;
    --card-light: #f7f7f5;
    --teal: #0f948e;
    --ink: #141414;
    --paper-white: #e4e4e4;
    --divider-light: #d2d2d2;
  }
  * { box-sizing: border-box; margin: 0; padding: 0; }
  html, body {
    width: 1200px; height: 900px; overflow: hidden;
    background: var(--stage);
    font-family: "Archivo", Arial, sans-serif;
  }
  .stage {
    width: 1200px; height: 900px;
    display: flex; flex-direction: column; align-items: center; justify-content: center;
    gap: 54px;
  }
  .card {
    width: 600px; height: 343px;
    box-shadow: 0 14px 30px rgba(0,0,0,.55);
    position: relative;
  }
  .wordmark {
    font-weight: 800;
    text-transform: uppercase;
    line-height: .9;
    letter-spacing: .02em;
  }
  .wordmark span { display: block; }

  /* front */
  .card--front {
    background: var(--card-dark);
    display: flex; align-items: center; justify-content: center;
  }
  .card--front .wordmark { color: var(--paper-white); }
  .card--front .wordmark__lead { font-size: 112px; }
  .card--front .wordmark__line { font-size: 54px; }

  /* back */
  .card--back { background: var(--card-light); display: flex; }
  .card__brand {
    width: 300px; display: flex; align-items: center; justify-content: center;
    border-right: 1px solid var(--divider-light);
    margin: 40px 0;
  }
  .card--back .wordmark { color: var(--ink); }
  .card--back .wordmark__lead { font-size: 70px; }
  .card--back .wordmark__line { font-size: 34px; }
  .card__contact {
    flex: 1; padding: 58px 0 0 32px;
    color: var(--ink);
  }
  .contact__name {
    color: var(--teal); font-weight: 800; font-size: 20px;
    text-transform: uppercase; letter-spacing: .02em;
  }
  .contact__role { font-size: 16px; margin-bottom: 18px; }
  .contact__list { list-style: none; font-size: 15px; line-height: 1.55; }
  .contact__list li { display: flex; align-items: center; gap: 8px; }
  .contact__list svg { width: 14px; height: 14px; flex: none; }
  .accent { color: var(--teal); }
  .contact__address { margin-top: 20px; font-size: 15px; line-height: 1.4; }
</style>
</head>
<body>
<main class="stage">

  <section class="card card--front" aria-label="Card front">
    <h1 class="wordmark">
      <span class="wordmark__lead">VOR</span>
      <span class="wordmark__line">Exterior</span>
      <span class="wordmark__line">Coatings</span>
    </h1>
  </section>

  <section class="card card--back" aria-label="Card back">
    <div class="card__brand">
      <p class="wordmark">
        <span class="wordmark__lead">VOR</span>
        <span class="wordmark__line">Exterior</span>
        <span class="wordmark__line">Coatings</span>
      </p>
    </div>
    <div class="card__contact">
      <p class="contact__name">Marcus Delane</p>
      <p class="contact__role">Managing Director</p>
      <ul class="contact__list">
        <li>
          <svg viewBox="0 0 24 24" aria-hidden="true"><path fill="var(--teal)" d="M6.6 10.8a15 15 0 0 0 6.6 6.6l2.2-2.2a1 1 0 0 1 1-.25 11.4 11.4 0 0 0 3.6.57 1 1 0 0 1 1 1V20a1 1 0 0 1-1 1A17 17 0 0 1 3 4a1 1 0 0 1 1-1h3.5a1 1 0 0 1 1 1c0 1.25.2 2.45.57 3.57a1 1 0 0 1-.25 1z"/></svg>
          044-555 018 642
        </li>
        <li>
          <svg viewBox="0 0 24 24" aria-hidden="true"><rect x="2" y="5" width="20" height="14" rx="1" fill="var(--teal)"/><path d="M2 6l10 7 10-7" fill="none" stroke="var(--card-light)" stroke-width="2"/></svg>
          info@vorcoat.com
        </li>
        <li>
          <svg viewBox="0 0 24 24" aria-hidden="true"><g fill="none" stroke="var(--teal)" stroke-width="2"><circle cx="12" cy="12" r="9.5"/><ellipse cx="12" cy="12" rx="4" ry="9.5"/><path d="M2.5 12h19M4 7h16M4 17h16"/></g></svg>
          <span>www.<span class="accent">vorcoat</span>.com</span>
        </li>
      </ul>
      <p class="contact__address">88, Harbor Mill Road<br>30718, Northfield</p>
    </div>
  </section>

</main>
</body>
</html>
```